Kestrelway Financial Plans

I am looking for a complete resdesign of my small financial presentation. This is a Word Doc/PDF that I print off when meeting with people in private. I often present my "two pager" that I have been using for years and years. It tells them the basics of what I do, how I help people and foundational financial principles.

I have recently gone out on my own in business and have completely rebranded. This presentation is my most used tool, so it is the first of many things I would like to redo. I am hoping it will somehow coordinate with the colors of my business, not necessarily the EXACT same 3 colors everywhere, but have the design colors compliment.

I've uploaded all my logo designs, as well as the current "two-pager". I am not against it going to 3 pages if needed. As it will still land on 2 pages with duplex printing.

It has always been VERY simple. I am wanting it built into a more professional and design specific format, to show off my branding, without being over cluttered.

I am completely open to ANY graphics changes. Obviously some are very novice, the house on the last page has always been overly simplified.

```html
<!DOCTYPE html>
<html lang="en">
<head>
<meta charset="utf-8">
<title>Kestrelway Financial Plans – The Financial Challenge</title>
<link rel="stylesheet" href="https://fonts.googleapis.com/css2?family=Montserrat:wght@300;400;500;600;700;800;900&display=swap">
<style>
  :root{
    --stage:#8eadd7;
    --ink:#111a22;
    --body:#2b3138;
    --green:#1faa3f;
    --green-bright:#27c04a;
    --navy:#0d1e31;
    --mint:#dcf3e2;
    --card-line:#9aa4ad;
    --soft:#f2f3f3;
  }
  *{box-sizing:border-box;margin:0;padding:0}
  html,body{width:1200px;height:593px;overflow:hidden}
  body{background:var(--stage);font-family:"Montserrat",sans-serif;color:var(--body);position:relative}
  .abs{position:absolute}
  .panel{position:absolute;top:42px;width:360px;height:509px;overflow:hidden;
    background:linear-gradient(160deg,#ffffff 30%,var(--mint) 100%)}
  .panel--intro{left:43px}
  .panel--plan{left:420px}
  .panel--growth{left:797px}
  .art{position:absolute;border-radius:14px}
  .heavy{font-weight:900;color:var(--ink);letter-spacing:-.3px;line-height:.98}
  .heavy .accent{color:var(--green)}

  /* intro panel */
  .brand{left:28px;top:31px;color:var(--ink);font-weight:600;text-align:center;line-height:1}
  .brand__name{font-size:21px;letter-spacing:.5px}
  .brand__sub{font-size:7.5px;letter-spacing:2px;margin-top:5px;display:flex;align-items:center;gap:6px}
  .brand__sub::before,.brand__sub::after{content:"";width:18px;height:1.5px;background:var(--ink)}
  .hero-title{left:28px;top:82px;font-size:29px}
  .hero-banner{left:29px;top:137px;width:212px;height:38px;background:var(--green);transform:rotate(-2deg);
    color:#fff;font-weight:900;font-size:28px;line-height:38px;padding-left:9px;letter-spacing:-.3px}
  .fact-box{top:194px;width:151px;height:176px;border:1px solid var(--card-line);padding:10px 8px 0 8px;background:rgba(255,255,255,.6)}
  .fact-box--savings{left:25px}
  .fact-box--debt{left:184px}
  .fact-box h3,.insurance h3{font-weight:800;font-size:12px;color:var(--ink);margin-bottom:8px;letter-spacing:-.2px}
  .fact-box--debt h3{color:var(--green)}
  .facts{list-style:none;font-size:7.7px;font-weight:300;line-height:10.3px}
  .facts li{position:relative;padding-left:13px;margin-bottom:9px}
  .facts li::before{content:"";position:absolute;left:1px;top:1px;width:6px;height:3px;border-left:1.2px solid var(--ink);border-bottom:1.2px solid var(--ink);transform:rotate(-45deg)}
  .facts b{font-weight:700;color:var(--ink)}
  .insurance{left:33px;top:387px;width:300px}
  .insurance .facts li{margin-bottom:8px}

  /* plan panel */
  .challenge{left:16px;top:15px;width:330px;height:277px;background:var(--soft);border:1px solid #b9dcc3}
  .section-title{font-size:17px}
  .pillar{position:absolute;width:90px;text-align:center;font-size:6.6px;font-weight:300;line-height:8.2px}
  .pillar__icon{width:26px;height:28px;margin:0 auto 5px;border-radius:6px;background:linear-gradient(135deg,#e5e8ea,#c9cfd3)}
  .pillar__icon--green{background:linear-gradient(135deg,#c8efd3,#7fd598)}
  .pillar h4{font-weight:800;font-size:7.8px;line-height:7.6px;color:var(--ink);margin-bottom:5px}
  .pillar h4.green{color:var(--green)}
  .pillar .mid{font-weight:500;font-size:7.4px;color:var(--ink)}
  .pie-label{font-size:7px;font-weight:500;color:var(--ink);line-height:7px}
  .savings-label{font-weight:800;font-size:11px;color:var(--ink)}
  .line{position:absolute;background:#333}
  .goals{font-size:7px;font-weight:400;line-height:8.2px;color:var(--ink)}
  .goals span{display:block;position:relative;padding-left:11px}
  .goals span::before{content:"";position:absolute;left:0;top:1px;width:5px;height:5px;border:.8px solid #333}
  .carriers{left:201px;top:389px;width:144px;height:101px;border:1px solid #b9dcc3;background:#fff;
    display:grid;grid-template-columns:1fr 1fr;align-items:center;padding:5px 6px;column-gap:6px}
  .carrier{font-size:6.4px;font-weight:600;color:#1d3f8a;display:flex;align-items:center;gap:3px}
  .carrier i{width:5px;height:5px;border-radius:50%;background:#1d3f8a;flex:none}

  /* growth panel */
  .rule-band{left:0;top:0;width:360px;height:246px;background:var(--navy)}
  .rule-title{left:34px;top:33px;font-size:17px;color:#fff;font-weight:900}
  .rate{position:absolute;display:flex;align-items:center;gap:6px;color:#fff}
  .rate__pct{font-weight:900;font-size:17px;color:var(--green-bright);letter-spacing:-.5px}
  .rate__txt{font-weight:700;font-size:6.6px;line-height:7.6px}
  .ages{position:absolute;list-style:none;color:#fff;font-size:8px;font-weight:300;line-height:12px}
  .ages--tight{line-height:10px}
  .ages li{padding-left:10px;position:relative}
  .ages li::before{content:"";position:absolute;left:1px;top:4px;width:3px;height:3px;border-right:1px solid #fff;border-top:1px solid #fff;transform:rotate(45deg)}
  .divider{position:absolute;width:1px;background:#50627a}
  .structure-title{left:0;width:360px;top:266px;text-align:center;font-weight:900;font-size:18px;color:var(--green)}
  .pill{position:absolute;top:301px;width:119px;height:29px;border-radius:15px;background:#fff;box-shadow:0 1px 4px rgba(0,0,0,.12);
    text-align:center;font-size:7px;font-weight:800;line-height:7.6px;color:var(--ink);display:flex;flex-direction:column;justify-content:center}
  .pill .green{color:var(--green)}
  .conn{position:absolute;border-color:#555;border-style:solid;border-width:0}
  .vehicle{position:absolute;top:357px;width:71px;height:128px;border:1px solid var(--card-line);background:rgba(255,255,255,.75);
    text-align:center;padding-top:10px;font-size:6.6px;font-weight:300;line-height:7.4px;color:var(--body)}
  .vehicle h5{font-size:8.5px;font-weight:800;color:var(--ink);margin-bottom:8px}
  .vehicle h5.green{color:var(--green)}
  .vehicle p{margin-bottom:5px}
  .vehicle .outcome{position:absolute;left:0;right:0;bottom:8px;font-weight:900;color:#e0201b;font-size:11px;line-height:11px}
  .vehicle .outcome--sm{font-size:8.5px}
</style>
</head>
<body>

<!-- Panel one: the challenge -->
<section class="panel panel--intro">
  <div class="art" role="img" aria-label="3D blue bar chart with a green rising arrow and a stack of gold coins"
       style="left:212px;top:12px;width:142px;height:150px;background:radial-gradient(circle at 55% 60%,#6f8fe0 0%,#b8d8c0 55%,rgba(220,243,226,0) 75%)"></div>
  <div class="abs brand">
    <div class="brand__name">KESTRELWAY</div>
    <div class="brand__sub">FINANCIAL PLANS</div>
  </div>
  <h1 class="abs heavy hero-title">THE<br>FINANCIAL</h1>
  <div class="abs hero-banner">CHALLENGE</div>

  <div class="abs fact-box fact-box--savings">
    <h3>SAVINGS</h3>
    <ul class="facts">
      <li><b>49%</b> of Canadian employees are living pay-cheque to pay cheque. 25% of Canadians are unable to cover an unexpected $500 expense-Civic Data Bureau (Feb, 2023)</li>
      <li><b>25%</b> of Canadians need to access their retirement savings early. <b>20%</b> of Canadians have no savings. <b>39%</b> of Canadians aged 55-65 have less than <b>$5,000</b> in savings.</li>
    </ul>
  </div>
  <div class="abs fact-box fact-box--debt">
    <h3>DEBT</h3>
    <ul class="facts">
      <li>The average Canadian has <b>$22,131</b> in consumer debt. Which excludes mortgages. Ledgerline Credit (Aug. 2024)</li>
      <li>Over <b>55%</b> of Canadians hold credit card debt and the total Canadian household debt has increased to <b>$2.52</b> trillion, including consumer credit, mortgage &amp; non-mortgage loans. National Lenders Forum (Aug. 2024)</li>
    </ul>
  </div>
  <div class="abs insurance">
    <h3>INSURANCE</h3>
    <ul class="facts">
      <li><b>49%</b> of Canadians do not have individual life insurance coverage, but <b>48%</b> say their families would face financial trouble within 6 months of losing someone. Assurwise Research (apr. 2023)</li>
      <li>2-in-5 Canadians (<b>43%</b> women | <b>44%</b> men) will be diagosed with a form ofcancer or other critical illness during their lifetime. Every 7 seconds. Wellstat Registry (June 2024)</li>
    </ul>
  </div>
</section>

<!-- Panel two: the plan -->
<section class="panel panel--plan">
  <div class="abs challenge"></div>
  <div class="art" role="img" aria-label="Floating gold coins"
       style="left:234px;top:10px;width:118px;height:78px;background:radial-gradient(circle at 55% 45%,#f5c233 0%,#f8dd86 40%,rgba(242,243,243,0) 72%)"></div>
  <h2 class="abs heavy section-title" style="left:34px;top:33px">FACING THE<br><span class="accent">CHALLENGE</span></h2>

  <div class="pillar" style="left:38px;top:77px">
    <div class="pillar__icon" role="img" aria-label="Money bag icon"></div>
    <h4>CASH<br>FLOW</h4>
    <p>Analyze</p><p style="margin-top:3px">Free-Up<br>400% - 600%</p>
  </div>
  <div class="pillar" style="left:126px;top:77px">
    <div class="pillar__icon pillar__icon--green" role="img" aria-label="Money bag on gold bars icon"></div>
    <h4 class="green">BUILD<br>WEALTH</h4>
    <p class="mid">Financial<br>Independence<br>Number (F.I.N)</p>
  </div>
  <div class="pillar" style="left:219px;top:77px">
    <div class="pillar__icon" role="img" aria-label="Hands passing coins icon"></div>
    <h4>PRESENT<br>WEALTH</h4>
    <p class="mid">Analyze</p><p>Leaving a legacy</p>
    <p class="mid" style="margin-top:3px">Free-Up</p><p>Will Prep</p>
  </div>
  <div class="pillar" style="left:38px;top:173px">
    <div class="pillar__icon" role="img" aria-label="Umbrella over dollar coin icon"></div>
    <h4 class="green">CASH FLOW<br>PROTECTIN</h4>
    <p>Income Protection</p><p style="margin-top:4px">Life Insurance | CI &amp;<br>DI Insurance</p>
  </div>
  <div class="pillar" style="left:126px;top:173px">
    <div class="pillar__icon pillar__icon--green" role="img" aria-label="Debt chart icon"></div>
    <h4>DEBT<br>MANAGEMENT</h4>
    <p>20%</p><p style="margin-top:4px">6% - 7%</p>
  </div>
  <div class="pillar" style="left:219px;top:173px">
    <div class="pillar__icon" role="img" aria-label="Savings jar icon"></div>
    <h4 class="green">EMERGENCY<br>FUNDS</h4>
    <p class="mid">Analyze</p><p>If | When</p>
    <p class="mid" style="margin-top:3px">Free-Up</p><p>9 to 6 months</p>
  </div>
  <div class="art" role="img" aria-label="Hand holding a green banknote"
       style="left:292px;top:224px;width:70px;height:84px;background:linear-gradient(150deg,#b9e86a 0%,#e9c9a4 70%,rgba(255,255,255,0) 100%)"></div>

  <h2 class="abs heavy section-title" style="left:34px;top:314px">HOW WE WILL<br><span class="accent">DOING IT?</span></h2>

  <div class="abs pie-label" style="left:17px;top:369px">Living<br>Expanses</div>
  <div class="abs pie-label" style="left:61px;top:361px">Debt</div>
  <div class="abs pie-label" style="left:99px;top:370px">Taxes</div>
  <svg class="abs" style="left:30px;top:374px" width="100" height="100" viewBox="0 0 100 100" role="img" aria-label="Pie chart of living expenses, debt, taxes and savings">
    <path d="M50 50 L78.93 84.47 A45 45 0 1 1 50 5 Z" fill="#9ee9d2"/>
    <path d="M50 50 L50 5 A45 45 0 0 1 72.5 11.03 Z" fill="#8fd3ef"/>
    <path d="M50 50 L72.5 11.03 A45 45 0 0 1 92.29 34.61 Z" fill="#8aaef0"/>
    <path d="M50 50 L92.29 34.61 A45 45 0 0 1 78.93 84.47 Z" fill="#b3e1f3" transform="translate(5 2)"/>
  </svg>
  <div class="abs savings-label" style="left:129px;top:413px">SAVINGS</div>

  <div class="line" style="left:185px;top:354px;width:1px;height:96px"></div>
  <div class="line" style="left:185px;top:354px;width:12px;height:1px"></div>
  <div class="line" style="left:185px;top:449px;width:16px;height:1px"></div>
  <div class="line" style="left:172px;top:421px;width:13px;height:1px"></div>

  <div class="abs goals" style="left:201px;top:331px"><span>Retirement<br>Savings</span><span style="margin-top:2px">&nbsp;<br>Children's<br>Education</span></div>
  <div class="abs goals" style="left:265px;top:331px"><span>Proper Protection</span><span style="margin-top:5px">Freedom<br>from Debt</span></div>

  <div class="abs carriers">
    <div class="carrier"><i></i>Harbourmutual</div>
    <div class="carrier"><i></i>Northgate Life</div>
    <div class="carrier"><i></i>Maplecrest Insurance</div>
    <div class="carrier"><i></i>Rivermont</div>
    <div class="carrier"><i></i>Brightfield Financial</div>
    <div class="carrier"><i></i>Crownvale Insurance</div>
    <div class="carrier"><i></i>Solvio</div>
    <div class="carrier"><i></i>Altaris Groupe</div>
    <div class="carrier"><i></i>Pinecoast Life</div>
    <div class="carrier"><i></i>Veranta</div>
  </div>
</section>

<!-- Panel three: growth and structure -->
<section class="panel panel--growth">
  <div class="abs rule-band"></div>
  <div class="art" role="img" aria-label="Stack of green banknotes with gold coins and a green arrow"
       style="left:248px;top:14px;width:112px;height:130px;background:radial-gradient(circle at 50% 50%,#7bd36a 0%,#2f6a4a 45%,rgba(13,30,49,0) 72%)"></div>
  <h2 class="abs rule-title">RULE OF 72</h2>

  <div class="rate" style="left:35px;top:63px"><span class="rate__pct">4%</span><span class="rate__txt">MONEY DOUBLES<br>EVERY 18 YEARS</span></div>
  <ul class="ages" style="left:35px;top:85px"><li>Age 29 | $10,000</li><li>Age 47 | $20,000</li><li>Age 65 | $40,000</li></ul>
  <div class="divider" style="left:141px;top:62px;height:62px"></div>

  <div class="rate" style="left:153px;top:63px"><span class="rate__pct">6%</span><span class="rate__txt">MONEY DOUBLES<br>EVERY 12 YEARS</span></div>
  <ul class="ages ages--tight" style="left:153px;top:85px"><li>Age 29 | $10,000</li><li>Age 41 | $20,000</li><li>Age 53 | $40,000</li><li>Age 65 | $80,000</li></ul>

  <div class="rate" style="left:35px;top:147px"><span class="rate__pct">8%</span><span class="rate__txt">MONEY DOUBLES<br>EVERY 9 YEARS</span></div>
  <ul class="ages" style="left:35px;top:170px"><li>Age 29 | $10,000</li><li>Age 38 | $20,000</li><li>Age 47 | $40,000</li><li>Age 56 | $80,000</li><li>Age 6 | $160,000</li></ul>
  <div class="divider" style="left:141px;top:147px;height:110px;display:none"></div>
  <div class="divider" style="left:141px;top:172px;height:48px"></div>

  <div class="rate" style="left:153px;top:147px"><span class="rate__pct">12%</span><span class="rate__txt">MONEY DOUBLES<br>EVERY 9 YEARS</span></div>
  <ul class="ages" style="left:153px;top:170px"><li>Age 29 | $10,000</li><li>Age 35 | $20,000</li><li>Age 41 | $40,000</li><li>Age 47 | $80,000</li></ul>
  <ul class="ages" style="left:246px;top:170px"><li>Age 53 | $160,000</li><li>Age 59 | $320,000</li><li>Age 65 | $640,000</li></ul>

  <h2 class="abs structure-title">STRUCTURE</h2>
  <div class="pill" style="left:37px"><span class="green">LIFE INSURANCE ILLNESS</span><span>CRITICAL | DISABILITY</span></div>
  <div class="pill" style="left:208px"><span class="green">DEBT MANAGEMENT</span><span>CASH FLOW</span></div>

  <div class="conn" style="left:96px;top:331px;height:10px;border-left-width:1px;border-style:dashed"></div>
  <div class="conn" style="left:57px;top:341px;width:80px;height:9px;border-width:1px 1px 0 1px;border-style:dashed"></div>
  <div class="conn" style="left:267px;top:331px;height:10px;border-left-width:1px;border-style:dashed"></div>
  <div class="conn" style="left:228px;top:341px;width:80px;height:9px;border-width:1px 1px 0 1px;border-style:dashed"></div>

  <div class="vehicle" style="left:22px">
    <h5>HOME</h5>
    <p>Partner with<br>Mortgage</p><p>Brokers for<br>best rates</p>
    <p style="margin-top:12px">Mortgage<br>Insurance</p><p style="margin-top:6px">Alternatives</p>
    <div class="outcome outcome--sm">SELL</div>
  </div>
  <div class="vehicle" style="left:101px">
    <h5 class="green">RRSP</h5>
    <p>Tax Deduction</p><p style="margin-top:7px">Brokers for<br>best rates</p>
    <div class="outcome">100%<br>TAX</div>
  </div>
  <div class="vehicle" style="left:193px">
    <h5>TFSA</h5>
    <p>No Tax<br>Deduction</p><p style="margin-top:6px">Tax Free Growth</p>
    <p style="margin-top:6px">200<br>$95,000</p><p style="margin-top:4px">Limit 2023<br>$7,000 per year</p>
    <div class="outcome">0% TAX</div>
  </div>
  <div class="vehicle" style="left:272px">
    <h5 class="green">PERM LIFE</h5>
    <p>No Tax<br>Deduction</p><p style="margin-top:6px">Qualify</p><p style="margin-top:6px">Tax Deferred<br>Growth</p>
    <div class="outcome">0% TAX</div>
  </div>
</section>

</body>
</html>
```